Marwick Law Letterhead

We need a new letterhead design for a Law Firm. The address for the law firm is 1475 Calloway Street, Suite 210, Houston, Texas 77041. Phone Number: 832-361-9027; Fax Number: 832-614-7359. The logo is uploaded to the project.

```html
<!DOCTYPE html>
<html lang="en">
<head>
<meta charset="utf-8">
<title>Marwick Law Letterhead</title>
<link href="https://fonts.googleapis.com/css2?family=Montserrat:wght@400;500;600&display=swap" rel="stylesheet">
<style>
  :root {
    --navy: #1f3a73;
    --red: #c8202c;
    --red-dark: #8e1019;
    --ink: #222222;
    --paper: #ffffff;
    --backdrop: #ececee;
  }
  html, body {
    margin: 0;
    padding: 0;
    width: 1200px;
    height: 960px;
    overflow: hidden;
    background: var(--backdrop);
    font-family: "Montserrat", sans-serif;
  }
  .letterhead {
    position: absolute;
    left: 282px;
    top: 30px;
    width: 636px;
    height: 900px;
    background: var(--paper);
    box-shadow: 0 4px 18px rgba(0,0,0,0.12);
    overflow: hidden;
    color: var(--ink);
  }
  .brand {
    position: absolute;
    left: 44px;
    top: 58px;
    display: flex;
    align-items: center;
    gap: 10px;
  }
  .brand-dot {
    width: 30px;
    height: 30px;
    border-radius: 50%;
    background: var(--navy);
  }
  .brand-name {
    font-weight: 600;
    font-size: 26px;
    color: var(--navy);
    letter-spacing: 0.5px;
  }
  .contact {
    position: absolute;
    left: 440px;
    top: 40px;
    font-size: 10.5px;
    line-height: 1.4;
  }
  .contact-line {
    display: flex;
    align-items: center;
    gap: 6px;
    margin-top: 2px;
  }
  .contact-line svg { width: 10px; height: 10px; }
  .contact-address { margin-bottom: 4px; }
  .header-rule {
    position: absolute;
    left: 130px;
    top: 128px;
    width: 470px;
    height: 2px;
    background: var(--red);
  }
  .letter {
    position: absolute;
    left: 110px;
    top: 190px;
    width: 400px;
    font-size: 10.5px;
    line-height: 1.55;
  }
  .recipient { margin: 0 0 4px; }
  .letter p { margin: 0 0 16px; }
  .sign-off { margin-top: 26px; font-size: 11.5px; }
  .signature {
    width: 120px;
    height: 30px;
    margin-top: 8px;
    border-radius: 4px;
    background: linear-gradient(90deg, #e6e6e6, #f4f4f4);
  }
  .wave {
    position: absolute;
    left: 0;
    top: 0;
    width: 636px;
    height: 900px;
  }
</style>
</head>
<body>
  <main class="letterhead">
    <svg class="wave" viewBox="0 0 636 900" aria-hidden="true">
      <defs>
        <linearGradient id="redFade" x1="0" y1="0" x2="1" y2="1">
          <stop offset="0" stop-color="#d4222d"/>
          <stop offset="1" stop-color="#8e1019"/>
        </linearGradient>
      </defs>
      <path d="M385,900 C390,800 460,750 540,690 C610,635 640,560 636,470 L636,900 Z" fill="url(#redFade)"/>
      <path d="M368,900 C372,790 450,735 528,676 C598,622 626,550 612,440" fill="none" stroke="#1f3a73" stroke-width="5"/>
    </svg>

    <div class="brand">
      <span class="brand-dot"></span>
      <span class="brand-name">Marwick Law</span>
    </div>

    <div class="contact">
      <div class="contact-address">1475 Calloway Street,<br>Suite 210, Houston,<br>Texas 77041</div>
      <div class="contact-line">
        <svg viewBox="0 0 10 10"><path d="M2 1 L4 1 L4.6 3 L3.4 3.8 Q4.6 6 6.2 6.6 L7 5.4 L9 6 L9 8 Q5 9 1 3 Z" fill="#c8202c"/></svg>
        <span>832-361-9027</span>
      </div>
      <div class="contact-line">
        <svg viewBox="0 0 10 10"><rect x="1" y="4" width="8" height="4.5" rx="1" fill="#c8202c"/><rect x="2.5" y="1" width="5" height="3" fill="#c8202c"/></svg>
        <span>832-614-7359</span>
      </div>
    </div>

    <div class="header-rule"></div>

    <section class="letter">
      <div class="recipient">Mr/s<br>First Name and Last Name<br>Company Name<br>Address</div>
      <p>Lorem ipsum dolor sit amet,consectetur adipiscing sed do eiusmod tempor incididunt laboreet dolore magna aliqua.Ut enim ad minim,veniam, quis nostrud exercitation ullamco laboris nisi ut aliquip exea commodo consequat.Lorem ipsum dolor sit amet,consectetur adipiscing sed do eiusmod tempor incididunt.labore et dolore magna aliqua. Ut enim</p>
      <p>Lorem ipsum dolor sit amet, consectetur adipiscing sed do eiusmod tempor incididunt labore et dolore magna aliqua. Ut enim ad minim veniam, quis nostrud exercitation ullamco laboris nisi ut aliquip exea commodo consequat.Duis aute irure dolor in reprehenderit in voluptate velit esse cillum irure dolor in reprehenderit in voluptate velit esse irure</p>
      <p>Lorem ipsum dolor sit amet, consectetur adipiscing sed do eiusmod tempor incididunt labore et dolore magna aliqua. consequat. Duis aute irure dolor in.reprehenderit in voluptate velit esse cillum dolore eu fugiat nulla pariatur. Excepteur sint occaecat cupidatat non proident, sunt in culpa qui officia deserunt mollit,</p>
      <p>Lorem ipsum dolor sit amet, consectetur adipiscing sed do eiusmod tempor incididunt labore et dolore magna aliqua. Ut enim Lorem ipsum dolor sit amet, consectetur adipiscing sed do eiusmod tempor incididunt labore et dolore magna aliqua. Ut enim Lorem ipsum aliqua.ipsum</p>
      <p>Lorem ipsum dolor sit amet, consectetur adipiscing sed do eiusmod tempor incididunt labore et dolore magna aliqua. Ut enim ad minim veniam, quis nostrud exercitation ullamco laboris nisi ut aliquip exea commodo consequat.Duis aute irure dolor in reprehenderit in voluptate velit esse cillum irure dolor in reprehenderit in voluptate velit esse irure</p>
      <div class="sign-off">Regards</div>
      <div class="signature" role="img" aria-label="Handwritten signature"></div>
    </section>
  </main>
</body>
</html>
```